ALL TYPES OF COMMERCIAL PLASTERING

TYPE OF BLOCK LETTERING WITH STAND OUT QUALITIES
WITH SOME TYPE OF LOGO
SOMETHING UNIQUE FOR THE BUILDING INDUSTRY.
QUALITY WORKMANSHIP
Updates

forgot to include my mobile phone number on my brief. could you add it to your design please MOBILE PH 0491 586 032

please let me make this quite clear ,the company name is harbourline linings and Fitouts PTY LTD. THE TYPE OF WORK WE WILL BE DOING IS COMMERCIAL PLASTERING.

Industry/Entity Type

Industry

Contact Information for Business Card

harbourline linings and fitouts P/L
marcus trelawny p.o.box 82 wendouree 3355 email address harbourlinelinings@mailcove.example
ABN 84 519 263 740 COMMERCIAL PLASTERING

```html
<!DOCTYPE html>
<html lang="en">
<head>
<meta charset="utf-8">
<title>Harbourline Linings and Fitouts – Business Card</title>
<link href="https://fonts.googleapis.com/css2?family=Cinzel:wght@700&family=Arimo:wght@400&display=swap" rel="stylesheet">
<style>
  :root {
    --page-bg: #e9ebee;
    --card-top: #58b4ec;
    --card-bottom: #2a86d2;
    --figure-tone: #1f5f95;
    --ink-dark: #0b0f14;
    --ink-light: #ffffff;
  }
  html, body {
    margin: 0;
    padding: 0;
    width: 1200px;
    height: 960px;
    overflow: hidden;
    background: var(--page-bg);
  }
  .canvas {
    position: relative;
    width: 1200px;
    height: 960px;
  }
  .card {
    position: absolute;
    left: 330px;
    top: 40px;
    width: 540px;
    height: 880px;
    overflow: hidden;
    background: linear-gradient(165deg, var(--card-top) 0%, #3d9ce0 45%, var(--card-bottom) 100%);
    box-shadow: 0 18px 40px rgba(0,0,0,0.18);
  }
  .worker-figure {
    position: absolute;
    left: 10px;
    top: 430px;
    width: 400px;
    height: 450px;
  }
  .brand {
    position: absolute;
    left: 44px;
    top: 130px;
  }
  .brand-mark {
    position: absolute;
    left: 0;
    top: 0;
    width: 96px;
    height: 96px;
  }
  .brand-name {
    position: absolute;
    left: 52px;
    top: 92px;
    margin: 0;
    width: 440px;
    font-family: "Cinzel", serif;
    font-weight: 700;
    font-size: 25px;
    line-height: 28px;
    letter-spacing: 0.5px;
    color: var(--ink-dark);
    text-transform: uppercase;
  }
  .trade {
    position: absolute;
    left: 104px;
    top: 300px;
    margin: 0;
    font-family: "Arimo", sans-serif;
    font-size: 17px;
    letter-spacing: 1.5px;
    color: var(--ink-light);
    text-transform: uppercase;
  }
  .person-name {
    position: absolute;
    left: 92px;
    top: 398px;
    margin: 0;
    font-family: "Arimo", sans-serif;
    font-weight: 400;
    font-size: 40px;
    color: var(--ink-dark);
  }
  .contact-list {
    position: absolute;
    left: 70px;
    top: 500px;
    margin: 0;
    padding: 0;
    list-style: none;
    font-family: "Arimo", sans-serif;
    font-size: 25px;
    line-height: 36px;
    color: var(--ink-light);
  }
</style>
</head>
<body>
<main class="canvas">
  <section class="card">
    <svg class="worker-figure" role="img" aria-label="Faint large illustration of a plasterer raising a trowel" viewBox="0 0 400 450" xmlns="http://www.w3.org/2000/svg">
      <defs>
        <radialGradient id="figureFade" cx="45%" cy="55%" r="60%">
          <stop offset="0%" stop-color="#1f5f95" stop-opacity="0.55"/>
          <stop offset="100%" stop-color="#1f5f95" stop-opacity="0"/>
        </radialGradient>
      </defs>
      <rect x="0" y="0" width="400" height="450" fill="url(#figureFade)"/>
    </svg>

    <header class="brand">
      <svg class="brand-mark" viewBox="0 0 96 96" xmlns="http://www.w3.org/2000/svg" aria-hidden="true">
        <circle cx="48" cy="48" r="42" fill="none" stroke="#0b0f14" stroke-width="5"/>
      </svg>
      <h1 class="brand-name">Harbourline Linings<br>and Fitouts P/L</h1>
    </header>

    <p class="trade">Commercial Plastering</p>

    <h2 class="person-name">marcus trelawny</h2>

    <ul class="contact-list">
      <li>0491 586 032</li>
      <li>ABN 84 519 263 740</li>
      <li>p.o.box 82 wendouree 3355</li>
      <li>harbourlinelinings@mailcove.example</li>
    </ul>
  </section>
</main>
</body>
</html>
```